Business cards for Norwegian software consultancy business

We are in need of business cards for our Norwegian consultancy company.
“Valto Brindex AS” specializes in software development, architecture and agile methodology, providing mostly on-site services at customers.
The cards should reflect a certain level of business professionalism with an elegant touch, while paying tribute to our modern and technological heritage. Our logo should be featured, as well as room for basic information about the cardholder and legal information of the company (company name, address and VAT number).
We would like our cards to reflect that we are a modern consulting company. It should present a professional image that people will remember. The texture and color pallette should reflect our professionalism and reliability, so we prefer a light color pallette with colors such as gray, white, blue and black. The number of colors used should however not be overwhelming, with the text being distinct and readable.
We are open to untraditional layouts and playful designs as long as they communicate the intent stated above.
You could also take a look at our website http://www.brindex.no for input on our visual profile.
Our logo is attached in the form of vectors and rasterized PNG. Please comment if you would like the black-white and/or inverted versions as well.
Industry/Entity Type
Architecture
Contact Information for Business Card
Company information:
Valto Brindex AS
Kvernlia 14, 3170 Sem
482 71 519
info@brindex.no
www.brindex.no
Employee information:
Full name
Title
Email
Phone
Font styles to use
Look and feel

```html
<!DOCTYPE html>
<html lang="no">
<head>
<meta charset="utf-8">
<title>Valto Brindex AS – Business Cards</title>
<link href="https://fonts.googleapis.com/css2?family=Open+Sans:wght@300;400;700&display=swap" rel="stylesheet">
<style>
  :root {
    --stage: #e7e4df;
    --card-dark: #000000;
    --card-light: #ffffff;
    --ink: #111111;
    --ink-soft: #222222;
    --accent: #4a9ad6;
    --white: #ffffff;
  }
  * { margin: 0; padding: 0; box-sizing: border-box; }
  html, body {
    width: 1200px; height: 749px; overflow: hidden;
    background: var(--stage);
    font-family: "Open Sans", Arial, sans-serif;
  }
  .stage { position: relative; width: 1200px; height: 749px; }

  .card { position: absolute; top: 200px; height: 309px; overflow: hidden; }
  .card--front { left: 40px; width: 546px; background: var(--card-dark); }
  .card--back { left: 621px; width: 544px; background: var(--card-light); }

  .brand { position: absolute; display: flex; align-items: center; gap: 14px; }
  .brand__mark { display: block; background: var(--accent); }
  .brand__name {
    font-weight: 300; letter-spacing: 2px; line-height: 1; white-space: nowrap;
  }
  .card--front .brand { left: 110px; top: 130px; }
  .card--front .brand__mark { width: 24px; height: 24px; }
  .card--front .brand__name { color: var(--white); font-size: 36px; }

  .card--back .brand { left: 26px; top: 45px; }
  .card--back .brand__mark { width: 22px; height: 22px; }
  .card--back .brand__name { color: var(--ink); font-size: 36px; }

  .holder { position: absolute; left: 132px; top: 138px; color: var(--ink-soft); font-size: 12.5px; line-height: 16px; }
  .holder__name { font-weight: 700; font-size: 14px; color: var(--ink); }
  .holder__title { margin-bottom: 14px; }
  .holder__address { margin-bottom: 4px; }

  .card__bands { position: absolute; left: 0; bottom: 0; width: 544px; height: 22px; }
</style>
</head>
<body>
<main class="stage">
  <section class="card card--front" aria-label="Card front">
    <div class="brand">
      <span class="brand__mark"></span>
      <span class="brand__name">VALTO BRINDEX</span>
    </div>
  </section>

  <section class="card card--back" aria-label="Card back">
    <div class="brand">
      <span class="brand__mark"></span>
      <span class="brand__name">VALTO BRINDEX</span>
    </div>
    <div class="holder">
      <p class="holder__name">Henrik Solvang</p>
      <p class="holder__title">Manger</p>
      <p class="holder__address">Valto Brindex AS Kvernlia<br>14, 3170 Sem 482 71 519</p>
      <p>t: + 47 912 34 567</p>
      <p>e: info@brindex.no</p>
      <p>www.brindex.no</p>
    </div>
    <svg class="card__bands" viewBox="0 0 544 22" aria-hidden="true">
      <polygon points="0,2 312,2 322,22 0,22" fill="var(--ink)"/>
      <polygon points="322,8 544,8 544,22 328,22" fill="var(--accent)"/>
    </svg>
  </section>
</main>
</body>
</html>
```